High-end executive coaching group needs a 2 page digital flyer

We need a 2 page digital flyer for a high end leadership coaching offering for global leaders in healthcare. The flyer will advertise a new service (an elite senior leadership coaching group) for senior leaders in the healthcare industry from around the world.
The flyer should be upmarket, professional and minimalist in style to meet the expectations of my professional market (very senior doctors and executives).
The design should be based on my existing logo and brand, see my landing page: www.marlowadvisory.com
The key elements needed are
1) An editable PDF which we can update as we revise the specific details of the offering. The text and draft design for this is attached.
2) The banner image should be high quality but abstract. It can be based on the landing page of my website (the two ripple effects) but does not need to strictly adhere to this.
3) The logo placement of the Marlow Advisory delta sign should be discreet so that it does not dominate
4) The small logos of our professional accrediting organisations should be discreetly placed at the end and should not dominate. They might work best as mono icons in a footer (e.g. blue on a white background, or white on blue.
5) Please find enclosed a previous flyer as an example of a similar style we have used for more junior professionals. The design worked quite well, although we now need a more upmarket version for our senior executives.

Please note this design specifically needs to use existing branding and images from my website: marlowadvisory.com. We are definitely not looking for stock "leadership team" images for this high-end brochure.

Target Market(s)

Senior global leaders in the healthcare industry

Industry/Entity Type

Leading business schools & Healthcare industry.

Font styles to use
Other font styles liked:
• Operetta (selective use for heading) and Sofia Pro (body text)

Colors
0054AA
0677BA
7BADD7
CADEEF
E8F1F8

Requirements
Must have
• Clean minimalist and high professionally look that directly speaks to the interests and perspectives of senior leader leaders in healthcare. It also needs very clear call to action sections
Nice to have
• Effective presentation of the two bios and photographs. These need to look impressive, but should not dominate.
Should not have
• Loud and bold colours, large use of logos.

```html
<!DOCTYPE html>
<html lang="en">
<head>
<meta charset="utf-8">
<title>Elevate and Ignite Your Leadership — Marlow Advisory</title>
<link rel="stylesheet" href="https://fonts.googleapis.com/css2?family=Cormorant+Garamond:wght@400;500&family=Outfit:wght@300;400;500;700&display=swap">
<style>
:root{
  --brand:#0054AA;
  --brand-mid:#0677BA;
  --sky:#7BADD7;
  --mist:#CADEEF;
  --ice:#E8F1F8;
  --panel:#DDE8F5;
  --ink:#3a4a63;
  --stage:#2b2b2b;
  --white:#ffffff;
}
*{box-sizing:border-box;margin:0;padding:0}
html,body{width:1200px;height:3027px;overflow:hidden;background:var(--stage)}
body{position:relative;font-family:"Outfit",sans-serif;font-weight:300;color:var(--ink)}
.page{position:absolute;left:154px;width:910px;background:var(--white);overflow:hidden}
.page--one{top:181px;height:1287px}
.page--two{top:1540px;height:1303px}
.abs{position:absolute}
.serif{font-family:"Cormorant Garamond",serif;font-weight:500}

/* page one */
.hero{left:0;top:0;width:910px;height:630px;
  background:
   radial-gradient(ellipse 70% 14% at 50% 49%, rgba(6,119,186,.45), transparent 70%),
   linear-gradient(180deg,#cfe3ee 0%,#e6f0f5 18%,#d8e6ef 32%,#8fb1d2 42%,#4f7fb8 47%,#a9c4de 52%,#dfe9f3 60%,#eef4f9 68%,#ffffff 82%)}
.hero-title{left:73px;top:42px;width:770px;height:44px;background:var(--white);
  font-size:37px;letter-spacing:1.2px;color:#2f4f7a;text-align:center;line-height:44px}
.hero-sub{left:0;top:357px;width:910px;text-align:center;color:var(--brand);font-size:22px;line-height:27.5px;font-weight:300}
.intro-card{left:45px;top:453px;width:813px;height:197px;background:var(--white);box-shadow:0 2px 6px rgba(0,0,0,.18)}
.intro-tab{left:107px;top:453px;width:696px;height:49px;background:var(--brand);
  clip-path:polygon(0 0,100% 0,96% 100%,4% 100%);color:var(--white);font-size:22px;text-align:center;line-height:49px;font-weight:300;letter-spacing:.3px}
.intro-text{left:45px;width:813px;text-align:center;font-size:15.5px;line-height:20.5px;color:#2d3440}
.benefits{left:45px;top:683px;width:508px;height:361px;background:var(--panel);padding:20px 30px 0 24px}
.benefits h2{font-weight:400;color:var(--brand);font-size:23px;letter-spacing:.5px;margin:0 0 8px 14px}
.benefits ul{list-style:none}
.benefits li{position:relative;padding-left:14px;font-size:15.5px;line-height:20px;color:#5a6b85}
.benefits li::before{content:"";position:absolute;left:2px;top:8px;width:5px;height:5px;border-radius:50%;background:var(--brand)}
.benefits b{font-weight:400;color:var(--brand)}
.date-bar{left:45px;top:1077px;width:508px;height:36px;background:var(--brand);color:var(--white);text-align:center;line-height:36px;font-size:16.5px;font-weight:400;letter-spacing:.4px}
.time-bar{left:45px;top:1116px;width:508px;height:38px;background:var(--panel);color:var(--brand);text-align:center;line-height:38px;font-size:16.5px;font-weight:400}
.details{left:67px;top:1172px;font-size:15.5px;line-height:20.5px;color:#5a6b85}
.details b{font-weight:400;color:var(--brand)}
.quote-box{border:1.5px solid var(--brand);background:var(--white);text-align:center}
.quote-mark{font-family:"Outfit",sans-serif;font-weight:700;color:var(--brand);font-size:96px;line-height:80px;height:48px;overflow:hidden;letter-spacing:-6px}
.quote-text{font-size:15.5px;line-height:20.4px;color:#5a6b85}
.quote-by{color:var(--brand);font-weight:400;font-size:16px}
.cta-blue{background:var(--brand);color:var(--white);text-align:center;font-size:18px;line-height:23px;font-weight:400;letter-spacing:.3px}
.brand-mark{display:flex;align-items:center;gap:14px}
.brand-mark .dot{width:16px;height:16px;border-radius:50%;background:var(--brand)}
.brand-mark .name{font-family:"Cormorant Garamond",serif;font-weight:500;color:var(--brand);font-size:28px;line-height:25px}

/* page two */
.guide-band{left:36px;top:34px;width:845px;height:42px;background:var(--brand);color:var(--white);text-align:center;line-height:42px;font-size:17px;letter-spacing:.4px}
.bio{top:94px;height:582px;border:1.5px solid var(--brand);background:var(--white)}
.bio-photo{position:absolute;left:50%;top:25px;width:184px;height:184px;margin-left:-92px;border-radius:50%;background:var(--white);box-shadow:0 0 5px rgba(0,0,0,.18)}
.bio-photo span{position:absolute;left:8px;top:8px;width:168px;height:168px;border-radius:50%;display:block}
.bio h3{position:absolute;top:222px;left:0;width:100%;text-align:center;color:var(--brand);font-weight:400;font-size:24px;letter-spacing:.4px}
.bio p{position:absolute;top:270px;left:30px;right:30px;text-align:justify;font-size:15.6px;line-height:20.5px;color:#5a6b85;hyphens:auto}
.explore{left:64px;top:700px;font-size:15.5px;line-height:21px;color:#2d3440}
.explore ul{list-style:none;margin-top:12px}
.explore li::before{content:"\2022  ";color:var(--brand)}
.spots{left:36px;top:827px;width:410px;height:238px;background:var(--panel)}
.spots-bar{position:absolute;left:24px;top:37px;width:369px;height:47px;background:var(--brand);color:var(--white);text-align:center;line-height:47px;font-size:20px;font-weight:400}
.spots-text{position:absolute;left:0;top:112px;width:100%;text-align:center;color:var(--brand);font-size:22px;line-height:26px;font-weight:400}
.badges{left:545px;top:1106px;display:flex;gap:22px;align-items:center}
.badge{background:var(--brand);opacity:.85}
.footer-light{left:0;top:1184px;width:910px;height:119px;background:var(--ice)}
.footer-cta{left:0;top:1184px;width:460px;height:119px;background:var(--brand);clip-path:polygon(0 0,85% 0,100% 100%,0 100%)}
.footer-cta span{position:absolute;left:66px;top:30px;color:var(--white);font-size:32px;line-height:31px;letter-spacing:.6px}
.contact{left:578px;top:1208px;font-size:16.5px;line-height:22px;color:var(--brand);font-weight:400}
.contact div{display:flex;align-items:center;gap:8px}
.web{left:603px;top:1266px;font-size:21px;color:var(--brand);font-weight:400}
</style>
</head>
<body>

<section class="page page--one">
  <div class="abs hero" role="img" aria-label="Abstract watercolour banner of soft blue ripples and mirrored hills"></div>
  <h1 class="abs hero-title serif">ELEVATE AND IGNITE YOUR LEADERSHIP</h1>
  <p class="abs hero-sub">TRANSFORMATIVE CONVERSATIONS FOR SENIOR HEALTHCARE LEADERS.<br>UNLOCK PURPOSE, ENGAGE AUTHENTICALLY AND<br>AMPLIFY YOUR LEADERSHIP IMPACT.</p>

  <div class="abs intro-card"></div>
  <div class="abs intro-tab">ANALYTIC COACHING GROUP FOR SENIOR LEADERS</div>
  <p class="abs intro-text" style="top:524px">As a senior leader in healthcare, you’re constantly navigating challenges.<br>But where do you turn for authentic connections, reflection and personal growth?</p>
  <p class="abs intro-text" style="top:584px">Rethink your leadership assumptions and approach challenges with fresh creativity.<br>Secure your spot in our exclusive Analytic Coaching Group and ignite your leadership potential.</p>

  <div class="abs benefits">
    <h2>BENEFITS</h2>
    <ul>
      <li><b>Transformative conversations:</b><br>Engage in discussions that spark innovative leadership</li>
      <li><b>Peer insights:</b><br>Harness fresh insights from peers, enhancing your decision-making and effectiveness</li>
      <li><b>Reimagined leadership:</b><br>Channel your creativity and redefine your leadership, personally and professionally</li>
      <li><b>Instant 360° insights:</b><br>Gain real-time feedback from trusted peers to enrich your leadership</li>
      <li><b>Lead authentically:</b><br>Develop effective strategies using the latest insights from group and leadership psychology</li>
    </ul>
  </div>

  <div class="abs date-bar">7 FEBRUARY 2024 – 11 DECEMBER 2024</div>
  <div class="abs time-bar">TIME: 7:30AM - 8:45AM (UK TIME)</div>
  <div class="abs details">
    <b>Commitment</b> : Wednesdays, every 2 weeks<br>
    <b>Location</b> &nbsp;&nbsp;&nbsp;&nbsp;&nbsp;&nbsp;: Connect from anywhere by Meetline<br>
    <b>COST: £3350 [UK] €3900 [EUROPE] A$6530 [AUSTRALIA]</b><br>
    Payment options available
  </div>

  <div class="abs quote-box" style="left:578px;top:683px;width:287px;height:470px;">
    <div class="quote-mark" style="margin-top:26px">”</div>
    <p class="quote-text" style="margin-top:58px;padding:0 22px">“You bare your heart<br>and share things you wouldn’t under normal circumstances. You get to know each other very quickly. There’s that sort of intense, shared experience that comes from speaking to each other’s lives.”</p>
    <p class="quote-by" style="margin-top:24px">Sarah, Medical Director</p>
  </div>
  <div class="abs cta-blue" style="left:578px;top:1044px;width:287px;height:109px;padding-top:20px">SECURE YOUR SPOT NOW<br>AND IGNITE YOUR<br>LEADERSHIP POTENTIAL</div>

  <div class="abs brand-mark" style="left:622px;top:1195px">
    <span class="dot"></span><span class="name">Marlow<br>Advisory</span>
  </div>
</section>

<section class="page page--two">
  <div class="abs guide-band serif">EXPERTLY GUIDED BY INSIGHT, ACADEMIC RIGOUR &amp; PRACTICAL LEADERSHIP STRATEGIES</div>

  <article class="abs bio" style="left:36px;width:410px">
    <div class="bio-photo"><span role="img" aria-label="Portrait photograph of Prof. Daniel Marlow" style="background:radial-gradient(circle at 50% 45%,#c9a48c 0%,#8a9a7a 45%,#4f6d4a 100%)"></span></div>
    <h3>PROF. DANIEL MARLOW</h3>
    <p>Professor Daniel Marlow has 30 years’ experience developing leaders. An award-winning business school professor, group analyst and psychoanalytic psychotherapist, he has taught senior leadership programmes at the University of Northbridge, Kingsmere College London and the University of Eastvale. His extensive leadership experience as a national health service clinical director and consultant psychotherapist inform his work as an GCF accredited executive coach. With a PhD from Regent College, University of Westmoor, he is an expert in melding psychological insights with strategic organisational change.</p>
  </article>

  <article class="abs bio" style="left:470px;width:412px">
    <div class="bio-photo"><span role="img" aria-label="Portrait photograph of Dr. Helen Ashcroft" style="background:radial-gradient(circle at 50% 45%,#c89c86 0%,#6b3f30 45%,#1e1814 100%)"></span></div>
    <h3>DR. HELEN ASHCROFT</h3>
    <p>Dr Helen Ashcroft is a renowned psychoanalyst, group analyst, consultant psychiatrist and organisational consultant in the health sector. She has 20 years of leadership within the national health service, and she was also the National Director of Therapies for the Elmstead Group, directing therapy services across 100 UK hospitals. She holds prominent positions as Chair of the Patient Safety Group, Chair of the Working Group on the Effect of Suicide and Homicide on Psychiatrists, and Vice Chair of the Psychotherapy Faculty at the Royal Society of Psychiatrists.</p>
  </article>

  <div class="abs explore">
    Engage with global leaders, gain diverse insights and forge lasting bonds. Explore questions such as:
    <ul>
      <li>What kind of leader do I aspire to be in the next chapter of my life and career?</li>
      <li>unique qualities and actions do I offer that no one else can?</li>
      <li>How can I galvanise my personal strengths to inspire and motivate others?</li>
    </ul>
  </div>

  <div class="abs spots">
    <div class="spots-bar">LIMITED SPOTS AVAILABLE</div>
    <p class="spots-text">DON’T MISS THIS UNIQUE<br>OPPORTUNITY TO TRANSFORM<br>YOUR LEADERSHIP JOURNEY.</p>
  </div>

  <div class="abs quote-box" style="left:470px;top:827px;width:412px;height:238px;">
    <div class="quote-mark" style="margin-top:16px">”</div>
    <p class="quote-text" style="margin-top:18px;padding:0 30px">“Through this exceptional coaching, our leadership team elevated its performance to lead the hospital with greater clarity, cohesion and thoughtfulness. Not only do we provide a superior work environment for staff, but better care for our patients.”</p>
    <p class="quote-by" style="margin-top:20px;font-weight:300;color:#2d3440">John, CEO</p>
  </div>

  <div class="abs brand-mark" style="left:66px;top:1110px">
    <span class="dot"></span><span class="name">Marlow<br>Advisory</span>
  </div>

  <div class="abs badges" aria-label="Accrediting organisations">
    <span class="badge" style="width:40px;height:40px;border-radius:50%"></span>
    <span class="badge" style="width:74px;height:30px"></span>
    <span class="badge" style="width:66px;height:34px"></span>
    <span class="badge" style="width:90px;height:28px"></span>
  </div>

  <div class="abs footer-light"></div>
  <div class="abs footer-cta"><span class="serif">BOOK YOUR FREE<br>DISCOVERY CALL</span></div>
  <div class="abs contact">
    <div><svg width="13" height="10" viewBox="0 0 13 10"><rect x=".6" y=".6" width="11.8" height="8.8" fill="none" stroke="#0054AA" stroke-width="1.2"/><path d="M.6 .6 6.5 5.5 12.4 .6" fill="none" stroke="#0054AA" stroke-width="1.2"/></svg>daniel@marlowadvisory.com</div>
    <div><svg width="13" height="10" viewBox="0 0 13 10"><rect x=".6" y=".6" width="11.8" height="8.8" fill="none" stroke="#0054AA" stroke-width="1.2"/><path d="M.6 .6 6.5 5.5 12.4 .6" fill="none" stroke="#0054AA" stroke-width="1.2"/></svg>helenashcroft@mailbox.com</div>
  </div>
  <div class="abs web">www.marlowadvisory.com</div>
</section>

</body>
</html>
```